Bright Paths Living Charity Golf Tournament

we are looking for help designing a trifold brochure that could accompany the attached letter, both being mailed in a #10 envelope. With the amount of sponsorship copy, it be a good idea to put the detailed sponsorship level content on a single one-page flyer. One section of the trifold could be a summary level of the sponsorship level and allow the sponsor tear-off that part and mail in their payment. I want the color scheme and design to align with our website https://brightpathsliving.org while not losing sight that this is a charity golf tournament. The sponsorship detail is not finalized but is directionally correct as shown on page 2 of the letter. What might be ideal is to have a tri-fold, a bi-fold which would contain details of the event along with the copy on the letter, while the one-page flyer would have the detailed sponsor levels & details.

I would also be open to alternative ideas if you think there's a better way of doing this. For example, could we put everything into a one 2-page brochure that would be the same size as the letter. There could be a tear out to mail back but this could fit into an envelope that could accommodate an unfolded 8.5x11 letter. I think this could work but will let you think about best options.

Target Market(s)

Corporate sponsors and serious golfers

Industry/Entity Type

Non-Profit

Font styles to use
Serif

Requirements
Must have
• Event Date: August 23, 2021
Event Location: Maple Ridge County Club, 47 Orchard Lane, Glenside PA
Schedule:
Lunch: 11:00
Shotgun Start: 12:30
Open Bar Reception: 5:00
Dinner: 6:00

At the moment, the sponsorship levels, pricing, and inclusions are directionally correct.

BPL Brand Colors:
#08143A
#FFCD35
#980909
#11808B
#3C2C83

Ok to use any images from the Maple Ridge CC website.
Nice to have
• We have a lot of copy & content to share, so I am not locked into a trifold - bifold concept if a single full size 2-sheet (8 pages) would work better as long as there would be a way for the sponsor to 'tear off' the summary order form. If you think the full size version is a better single option to go with our letter, I would like to use some images from our website along to give the event the seriousness it deserves while still being a golf tournament. This will be our first annual tournament although I am not sure that's important to include.
Should not have
• emojis, clip art.

```html
<!DOCTYPE html>
<html lang="en">
<head>
<meta charset="utf-8">
<title>Bright Paths Living Charity Golf Tournament</title>
<link href="https://fonts.googleapis.com/css2?family=Kanit:wght@500;600;700&family=Saira+Semi+Condensed:wght@600;700&family=Montserrat:wght@400;500;600;700&display=swap" rel="stylesheet">
<style>
:root{
  --navy:#08143A;
  --gold:#FFCD35;
  --red:#980909;
  --teal:#11808B;
  --purple:#3C2C83;
  --rose:#E06C80;
  --stage:#5a5a5a;
  --paper:#ffffff;
  --mist:#eeeff1;
  --ink:#2a2a2a;
  --soft:#d9dadc;
}
*{box-sizing:border-box;margin:0;padding:0}
html,body{width:1200px;height:3119px;overflow:hidden}
body{background:var(--stage);font-family:"Montserrat",sans-serif;color:var(--ink);position:relative}

/* ---------- outside spread ---------- */
.spread{position:absolute;left:60px;width:1080px;height:700px;background:var(--paper);overflow:hidden;box-shadow:0 6px 18px rgba(0,0,0,.35)}
.spread--outside{top:60px}
.spread--inside{top:840px}
.course-photo{position:absolute;inset:0;
  background:linear-gradient(to bottom,#ffffff 0%,#ffffff 16%,#dfe6e6 24%,#a9c0bd 32%,#6f9263 44%,#3d6a2f 58%,#2f5a24 74%,#3f7030 88%,#2d4f22 100%)}
.fold{position:absolute;top:0;bottom:0;left:540px;width:1px;background:rgba(255,255,255,.25)}
.program-mark{position:absolute;left:160px;top:145px;display:flex;align-items:center;gap:12px}
.program-mark__dot{width:54px;height:54px;border-radius:50%;background:var(--navy);flex:none}
.program-mark__name{font-weight:600;font-size:20px;color:var(--navy);line-height:1.1}
.site-url{position:absolute;bottom:20px;font-size:12px;letter-spacing:.32em;color:#fff}
.site-url--left{left:160px}
.site-url--right{left:700px}
.brand-name{position:absolute;left:540px;width:540px;top:60px;text-align:center;font-weight:600;font-size:30px;color:var(--navy);letter-spacing:.02em}
.brand-rule{position:absolute;left:700px;width:220px;top:102px;height:2px;background:var(--gold)}
.title-card{position:absolute;left:649px;top:164px;width:322px;height:300px;background:var(--navy);outline:2px solid var(--gold);outline-offset:-10px;text-align:center;font-family:"Kanit",sans-serif;padding-top:20px}
.title-card__charity{color:var(--gold);font-size:54px;font-weight:700;line-height:1}
.title-card__golf{color:#fff;font-size:80px;font-weight:700;line-height:.95;letter-spacing:.02em}
.title-card__tournament{color:#fff;font-size:36px;font-weight:600;line-height:1.1}
.title-card__date{color:#1aa5b3;font-size:32px;font-weight:600;line-height:1.5}
.event-location{position:absolute;left:540px;width:540px;top:488px;text-align:center;font-family:"Kanit",sans-serif;font-size:16px;line-height:1.3}
.event-location b{color:var(--gold);font-weight:500;display:block}
.event-location span{color:#fff;font-weight:500}
.schedule{position:absolute;left:614px;top:575px;width:393px;height:52px;border:1.5px dashed rgba(255,255,255,.8);display:flex;font-family:"Kanit",sans-serif;font-size:12px;color:#fff;font-weight:500}
.schedule__tag{position:absolute;left:50%;top:-12px;transform:translateX(-50%);background:var(--teal);color:#fff;font-size:11px;letter-spacing:.28em;padding:2px 14px;border-radius:10px}
.schedule__col{flex:1;padding:10px 22px;line-height:1.45}
.schedule__col + .schedule__col{border-left:1.5px dashed rgba(255,255,255,.8)}
.schedule__col em{font-style:normal;color:var(--gold)}

/* ---------- inside spread ---------- */
.panel{position:absolute;top:0;bottom:0;width:540px;overflow:hidden}
.panel--left{left:0;background:var(--paper)}
.panel--right{left:540px;background:var(--mist)}
.faded-course{position:absolute;left:0;right:0;bottom:0;height:320px;background:linear-gradient(to bottom,rgba(255,255,255,0) 0%,rgba(200,215,200,.55) 55%,rgba(175,198,170,.85) 100%)}
.ribbon{position:absolute;width:64px;height:86px;background:var(--purple);clip-path:polygon(0 0,100% 0,100% 100%,50% 88%,0 100%)}
.ribbon::after{content:"";position:absolute;left:8px;top:22px;width:48px;height:48px;border-radius:50%;background:#fff}
.panel--left .ribbon{left:26px;top:0}
.headband{position:absolute;left:100px;right:20px;top:14px;height:72px;background:var(--soft);text-align:right;padding:12px 18px 0 0;font-family:"Saira Semi Condensed",sans-serif;font-weight:700;font-size:28px;line-height:1}
.headband .line1{color:var(--purple)}
.headband .line2{color:var(--red)}
.letter{position:absolute;left:24px;right:24px;top:110px;font-size:7.2px;line-height:1.4;color:#333}
.letter p{margin-bottom:7px;text-align:justify}
.work-title{position:absolute;left:24px;top:470px;font-family:"Kanit",sans-serif;font-weight:500;font-size:24px;line-height:1.15;color:var(--teal)}
.work-copy{position:absolute;left:24px;right:24px;top:545px;font-size:7.2px;line-height:1.45;color:#333;text-align:justify}
.partners-title{position:absolute;left:0;right:0;top:18px;text-align:center;font-family:"Kanit",sans-serif;font-weight:700;font-size:46px;letter-spacing:.07em;color:#d3d4d7}
.partners{position:absolute;left:18px;right:18px;top:95px;display:flex;gap:14px}
.partner{flex:1;font-size:6.8px;line-height:1.4;color:#333;text-align:justify}
.partner__name{display:flex;align-items:center;justify-content:center;gap:5px;height:30px;font-weight:600;font-size:13px;color:var(--navy)}
.partner__name i{width:11px;height:11px;border-radius:50%;background:var(--navy);display:block}
.partner__label{text-align:center;color:var(--purple);font-weight:600;font-size:7px;margin:6px 0 4px}
.why-title{position:absolute;left:0;right:0;top:305px;text-align:center;font-family:"Kanit",sans-serif;font-weight:500;font-size:23px;line-height:1.1;color:var(--rose);letter-spacing:.02em}
.why-copy{position:absolute;left:22px;right:22px;top:375px;font-size:7.2px;line-height:1.45;color:#333;text-align:justify}
.why-copy p{margin-bottom:10px}

/* ---------- order form ---------- */
.order-form{position:absolute;left:100px;top:1620px;width:1000px;height:1150px;background:var(--paper);box-shadow:0 6px 18px rgba(0,0,0,.35);padding:26px 70px 0}
.order-form .ribbon{left:50px;top:0;width:104px;height:134px}
.order-form .ribbon::after{left:14px;top:36px;width:76px;height:76px}
.form-head{margin-left:180px;margin-right:-20px;height:110px;background:var(--mist);text-align:right;padding:14px 24px 0 0}
.form-head h1{font-family:"Saira Semi Condensed",sans-serif;font-weight:700;font-size:38px;line-height:1;color:var(--teal)}
.form-head p{font-size:14px;color:#444;margin-top:8px}
table{width:100%;border-collapse:collapse}
.levels{margin-top:18px}
.levels caption{font-style:italic;font-weight:700;font-size:13px;padding-bottom:4px}
.levels td{border:1px solid #777;vertical-align:top;font-size:11.2px;padding:5px 6px;line-height:1.32}
.levels td.level{width:170px;font-weight:700;font-size:11px}
.levels td.level span{display:block;width:13px;height:13px;border:1.5px solid #333;float:left}
.levels td.level div{margin-left:22px}
.levels td.price{width:70px;text-align:right;font-weight:700}
.levels ul{padding-left:30px}
.contact{margin-top:18px}
.contact td{border:1px solid #777;height:27px;font-size:11px;font-weight:700;padding:0 6px}
.contact td:first-child{width:145px}
.invoice-note{margin-top:14px;text-align:center;font-style:italic;font-weight:700;font-size:11.5px}
.sign{position:relative;height:48px;margin-top:24px;font-size:11.5px;font-weight:700}
.sign__line{position:absolute;top:0;height:16px;border-bottom:1px solid #333}
.sign__line--sig{left:0;width:420px}
.sign__line--date{left:520px;width:260px}
.sign__label{position:absolute;top:22px}
.payable{display:flex;font-size:11.5px;margin-top:4px}
.payable em{font-weight:700;width:270px;flex:none}
.payable div{line-height:1.35}
.return-note{margin-top:30px;text-align:center;font-size:11.5px}
</style>
</head>
<body>

<section class="spread spread--outside" aria-label="Brochure outside">
  <div class="course-photo" role="img" aria-label="Photo of Maple Ridge County Club clubhouse and tree-lined fairway on a summer evening"></div>
  <div class="fold"></div>
  <div class="program-mark"><span class="program-mark__dot"></span><span class="program-mark__name">Guiding<br>Lights</span></div>
  <div class="site-url site-url--left">www.brightpathsliving.org</div>

  <div class="brand-name">Bright Paths Living</div>
  <div class="brand-rule"></div>
  <div class="title-card">
    <div class="title-card__charity">CHARITY</div>
    <div class="title-card__golf">GOLF</div>
    <div class="title-card__tournament">TOURNAMENT</div>
    <div class="title-card__date">AUGUST 23, 2021</div>
  </div>
  <div class="event-location">
    <b>Event Location:</b>
    <span>Maple Ridge County Club, 47 Orchard Lane, Glenside PA</span>
  </div>
  <div class="schedule">
    <span class="schedule__tag">SCHEDULE</span>
    <div class="schedule__col"><em>LUNCH:</em> 11:00<br><em>SHOTGUN START:</em> 12:30</div>
    <div class="schedule__col"><em>OPEN BAR RECEPTION:</em> 5:00<br><em>DINNER:</em> 6:00</div>
  </div>
  <div class="site-url site-url--right">www.brightpathsliving.org</div>
</section>

<section class="spread spread--inside" aria-label="Brochure inside">
  <div class="panel panel--left">
    <div class="faded-course" role="img" aria-label="Faded photo of a golf course fairway"></div>
    <div class="ribbon"></div>
    <div class="headband"><div class="line1">2021 HYBRID GOLF EVENT</div><div class="line2">SPONSORSHIP PROPOSAL</div></div>
    <div class="letter">
      <p>Dear Potential Sponsor:</p>
      <p>The Bright Paths Living Guiding Lights Committee is planning a Charity Hybrid Golf Tournament benefiting adults with autism or other intellectual developmental disabilities in Bucks and Lehigh County. The tournament will be held on Monday, August 23, at the Maple Ridge County Club in Glenside PA.</p>
      <p>Our mission is to offer adults with autism or other intellectual developmental disabilities the opportunity to live as independently as possible by providing safe and secure neuro-inclusive cohousing communities with built-in amenities and natural support systems, and to give their parents and aging caregivers peace of mind that they will never have to worry about their children being alone or isolated.</p>
      <p>We are actively confronting the unique and unmet housing needs and challenges higher-functioning autistic adults and other at-risk individuals face when their parents can no longer care for them. Instead, we provide neuro-inclusive smart-home enabled cohousing communities for this underserved population, allowing them to not only live as independently as possible, but seek meaningful employment and be an integral and active part of their local community.</p>
      <p>We are pleased to announce we have partnered with Harbor Giving Fund, FairwayTrack.org, and Greenlinks Clubs as our tournament partners. In addition to our in-person event on August 23, golfers can also play at 6 other local courses including Stonebrook National and Willow Creek, two nationally recognized Greenlinks private courses from August 1 - 23. Your sponsorship and company logo will be displayed on our tournament website from June 1 through August 31, and on the players mobile scoring app throughout the tournament.</p>
      <p>Please join Bright Paths Living in sponsoring the 2021 Guiding Lights Charity Golf Tournament. We have many different sponsorship levels available (please see the attached document). Help us provide safe and sustainable neuro-inclusive co-housing communities for adults with autism by completing the attached Sponsorship form. In order to secure the hole signs, pin flags, banners, and other custom sponsorship items, we would ask that you return it no later than June 1.</p>
      <p>Thank you for your consideration!</p>
      <p style="margin-top:14px">Guiding Lights Committee Chair</p>
    </div>
    <div class="work-title">About the work we're<br>doing at Bright Paths Living</div>
    <div class="work-copy">Every home we build begins with a family asking what happens next. Our communities pair private apartments with shared spaces, on-site support and links to local employers, so residents can grow their skills, keep their routines and build friendships that last. Sponsor support funds planning, staffing and the first resident homes in Bucks and Lehigh County, and helps us reach more families each year.</div>
  </div>

  <div class="panel panel--right">
    <div class="faded-course" role="img" aria-label="Faded photo of a golf course green"></div>
    <div class="partners-title">OUR PARTNERS</div>
    <div class="partners">
      <div class="partner">
        <div class="partner__name"><i></i>Harbor Giving</div>
        <div class="partner__label">Harbor Giving Fund</div>
        a 501(c)(3) nonprofit organization with a Platinum rating from a leading charity guide. It has been serving other nonprofit organizations for over 20 years and has donated over $38 million for worthy causes, and has been a partner to Bright Paths Living for 2 years.
      </div>
      <div class="partner">
        <div class="partner__name"><i></i>FairwayTrack</div>
        <div class="partner__label">FairwayTrack.org</div>
        The sport has, for decades, brought people together, rallying individuals, communities, and businesses around efforts that focus resources on under-served communities. In short, golf is a powerful force for good. FairwayTrack.org helps charities, foundations, associations, social clubs, civic groups, and other nonprofits harness that power.
      </div>
      <div class="partner">
        <div class="partner__name"><i></i>Greenlinks</div>
        <div class="partner__label">Greenlinks Clubs</div>
        the largest owner and operator of more than 200 private golf and country clubs, city, and stadium clubs in markets all across the country. Bringing people together is their passion. They are a community and lifestyle for golfers, thought leaders, foodies, dynamic women, young executives, and families.
      </div>
    </div>
    <div class="why-title">WHY IT'S IMPORTANT FOR<br>LOCAL BUSINESSES TO SPONSOR.</div>
    <div class="why-copy">
      <p>A local sponsorship puts your company name in front of golfers, families and business leaders who live and work in your own market. It shows customers and staff that you care about the community you serve, and it builds goodwill that lasts well beyond a single day on the course. Your brand appears on signage, carts, flags, the scoring app and our event website all summer long.</p>
      <p>Sponsors also gain direct access to a room of engaged decision makers. Foursomes, the reception and dinner give your team time to meet peers, clients and partners in a relaxed setting. Many of our sponsors tell us these conversations turn into long working relationships. Because we are a 501(c)(3) public charity, your sponsorship is tax deductible to the extent allowed by law, and every dollar supports housing, staffing and programs for adults with autism and other intellectual developmental disabilities here at home.</p>
      <p>Most of all, your support sends a clear message: that every adult deserves a safe place to live, meaningful work and a community that welcomes them. Join us on August 23 and help us turn a great round of golf into lasting change for families across Bucks and Lehigh County.</p>
    </div>
  </div>
</section>

<section class="order-form" aria-label="Sponsorship opportunities form">
  <div class="ribbon"></div>
  <div class="form-head">
    <h1>2021 HYBRID GOLF EVENT<br>SPONSORSHIP OPPORTUNITIES</h1>
    <p>as a 501(c)3 public charity, your sponsorship is tax deductible to the</p>
  </div>

  <table class="levels">
    <caption>Please Check Box:</caption>
    <tr><td class="level"><span></span><div>Presenting Sponsor</div></td>
      <td><ul><li>Co-Naming rights of the event with Bright Paths Living Guiding Lights</li><li>Banner at course with corporate logo</li><li>Corporate information in participants gift bags</li><li>Two golf foursomes</li><li>Recognition on all of our marketing materials as event presenting sponsor</li><li>Recognition and speaking opportunity at post-tournament event dinner</li></ul></td>
      <td class="price">$7,500</td></tr>
    <tr><td class="level"><span></span><div>Presenting Co-Sponsor</div></td>
      <td><ul><li>Co-Sponsor naming of the event with Guiding Lights and event presenting sponsor</li><li>Banner at course with corporate logo</li><li>Putting green sponsorship banner</li><li>Corporate information in participants gift bags</li><li>Two golf foursomes</li><li>Recognition on all of our marketing materials as event presenting co-sponsor</li><li>Recognition at event dinner</li></ul></td>
      <td class="price">$5,000</td></tr>
    <tr><td class="level"><span></span><div>Technology Sponsor</div></td>
      <td><ul><li>Driving range sponsorship banner</li><li>One golf foursome</li><li>Recognition on all of our marketing materials as event technology sponsor</li><li>Recognition at event dinner</li></ul></td>
      <td class="price">$3,000</td></tr>
    <tr><td class="level"><span></span><div>Corporate Sponsor with Golf Foursome</div></td>
      <td><ul><li>One golf foursome</li><li>Hole sign</li><li>Recognition on all of our marketing materials</li></ul></td>
      <td class="price">$2,500</td></tr>
    <tr><td class="level"><span></span><div>Pin Flag Sponsor</div></td>
      <td><ul><li>Your logo on a custom pin flag - yours to keep after the event</li><li>Recognition on all of our marketing materials</li></ul></td>
      <td class="price">$2,500</td></tr>
    <tr><td class="level"><span></span><div>Golf Cart Sponsor</div></td>
      <td><ul><li>Your logo &amp; brand on all golf carts</li><li>Recognition on all of our marketing materials</li></ul></td>
      <td class="price">$2,500</td></tr>
    <tr><td class="level"><span></span><div>Corporate Sponsor without Golf Foursome</div></td>
      <td><ul><li>Hole sign</li><li>Recognition on all of our marketing materials</li><li>Dinner at event for four</li></ul></td>
      <td class="price">$1,500</td></tr>
    <tr><td class="level"><span></span><div>Cigar Roller Sponsor</div></td>
      <td><ul><li>Table sign at rolling table at registration and at post-event reception</li><li>Recognition</li></ul></td>
      <td class="price">$1,000</td></tr>
    <tr><td class="level"><span></span><div>Hole Sponsor</div></td>
      <td><ul><li>Custom sign at every tee box</li></ul></td>
      <td class="price">$500</td></tr>
  </table>

  <table class="contact">
    <tr><td>Company Name</td><td></td></tr>
    <tr><td>Contact Person</td><td></td></tr>
    <tr><td>Contact Phone</td><td></td></tr>
    <tr><td>Contact Email</td><td></td></tr>
    <tr><td>Billing Address</td><td></td></tr>
    <tr><td>City/State/Zip</td><td></td></tr>
  </table>

  <div class="invoice-note">Invoices will be sent to the billing address or email address given above.</div>

  <div class="sign">
    <div class="sign__line sign__line--sig">X</div>
    <div class="sign__line sign__line--date"></div>
    <div class="sign__label" style="left:0">Signature of Sponsor</div>
    <div class="sign__label" style="left:520px">Date</div>
  </div>

  <div class="payable">
    <em>Please make checks payable to:</em>
    <div>Bright Paths Living Golf Tournament<br>210 Elm Street Doylestown, PA 18901</div>
  </div>

  <div class="return-note">Please return your completed Sponsorship form June 1, 2021</div>
</section>

</body>
</html>
```